Improved Business Card, Government Contracting

We are looking to update the design of our business cards. We would like to create a template that can be used for future employees and easy to update.

Halvorsen Advisory Partners, LLC is a Service Disabled Veteran Owned Small Business with headquarters located in Ashcombe, MO. Our current website is www.hvadpt.com. We have contracts in KS and VA with expansion opportunities in various other states. Our primary line of work is within government contracting and providing consulting services to various organizations within the Bureau of Civic Readiness. We would like to project a professional image of our company that is consistent with the industry. Provided are previous versions of our business card template that shows our logo as well. We would like to make sure the information on the cards are easily noticeable .

Target Market(s)

Government Officials
Fellow Small Business Contractors
Large Business Contractors (ex. TQLB, Pellwick Darrow, Fenwey Marsh Colquitt)

Industry/Entity Type

Business

Contact Information for Business Card

Dale Forsyth
Office Manager
Halvorsen Advisory Partners
Ph: 555.204.7716
Email: d.forsyth@hvadpt.us
www.hvadpt.com

Requirements
Must have
• The business mailing address is:
• 48730 212th Crescent
• Ashcombe, MO 66091
Nice to have
• Embossed lettering

```html
<!DOCTYPE html>
<html lang="en">
<head>
<meta charset="utf-8">
<title>Halvorsen Advisory Partners — Business Card</title>
<link href="https://fonts.googleapis.com/css2?family=Lato:wght@400;700&display=swap" rel="stylesheet">
<style>
  :root {
    --bg: #e9e6e1;
    --navy: #2e3192;
    --ink: #000000;
    --yellow: #fff25c;
    --white: #ffffff;
  }
  * { box-sizing: border-box; margin: 0; padding: 0; }
  html, body {
    width: 1200px; height: 900px; overflow: hidden;
    background: var(--bg);
    font-family: "Lato", sans-serif;
  }
  .card {
    position: absolute; left: 250px;
    width: 700px; height: 400px;
    overflow: hidden;
    box-shadow: 0 10px 24px rgba(0,0,0,.25);
  }
  .card-front { top: 35px; background: var(--navy); }
  .card-back  { top: 465px; background: var(--ink); }

  /* front */
  .front-brand {
    position: absolute; left: 0; right: 0; top: 150px;
    display: flex; justify-content: center; align-items: center; gap: 14px;
  }
  .brand-square { width: 22px; height: 22px; background: var(--yellow); }
  .front-name {
    color: var(--yellow); font-weight: 700; font-size: 36px; letter-spacing: .3px;
  }
  .front-web {
    position: absolute; left: 0; right: 0; top: 250px; text-align: center;
    color: var(--white); font-size: 18px; letter-spacing: 10px;
  }

  /* back */
  .back-brand {
    position: absolute; left: 150px; top: 52px;
    color: var(--yellow); font-weight: 700; font-size: 22px;
  }
  .contact-list {
    position: absolute; left: 34px; top: 118px; list-style: none;
    color: var(--white); font-size: 20px; line-height: 30px;
  }
  .contact-list li { display: flex; align-items: center; gap: 10px; }
  .contact-list svg { width: 16px; height: 16px; fill: var(--yellow); }
  .holder {
    position: absolute; right: 34px; top: 182px; text-align: right;
  }
  .holder-name { color: var(--yellow); font-weight: 700; font-size: 24px; }
  .holder-title { color: var(--white); font-size: 20px; }
  .address {
    position: absolute; right: 34px; top: 246px; text-align: right;
    font-size: 21px; line-height: 27px; color: var(--white); font-style: normal;
  }
  .address-company { color: var(--yellow); }
  .bands { position: absolute; left: 0; bottom: 0; width: 700px; height: 400px; }
</style>
</head>
<body>

<section class="card card-front">
  <div class="front-brand">
    <span class="brand-square"></span>
    <span class="front-name">Halvorsen Advisory Partners</span>
  </div>
  <p class="front-web">www.hvadpt.com</p>
</section>

<section class="card card-back">
  <svg class="bands" viewBox="0 0 700 400" aria-hidden="true">
    <polygon points="0,258 250,338 700,392 700,400 0,400" fill="#2e3192"/>
    <polygon points="0,288 240,364 700,400 0,400" fill="#fff25c"/>
  </svg>

  <p class="back-brand">Halvorsen Advisory Partners</p>

  <ul class="contact-list">
    <li>
      <svg viewBox="0 0 16 16"><path d="M3 1h3l1 4-2 1a9 9 0 0 0 5 5l1-2 4 1v3a2 2 0 0 1-2 2A13 13 0 0 1 1 3a2 2 0 0 1 2-2z"/></svg>
      555.204.7716
    </li>
    <li>
      <svg viewBox="0 0 16 16"><path d="M1 3h14v10H1z M1 3l7 6 7-6" stroke="#000" stroke-width="1"/></svg>
      d.forsyth@hvadpt.us
    </li>
    <li>
      <svg viewBox="0 0 16 16"><circle cx="8" cy="8" r="7"/><path d="M1 8h14M8 1v14M8 1c-4 4-4 10 0 14M8 1c4 4 4 10 0 14" stroke="#000" stroke-width="1" fill="none"/></svg>
      www.hvadpt.com
    </li>
  </ul>

  <div class="holder">
    <p class="holder-name">Dale Forsyth</p>
    <p class="holder-title">Office Manager</p>
  </div>

  <address class="address">
    <span class="address-company">Halvorsen Advisory Partners</span><br>
    48730 212th Crescent<br>
    Ashcombe, MO 66091
  </address>
</section>

</body>
</html>
```